Yacht, Boats, Watersports company needs a redesign of business card

Hello Designers!
We are a Boat dealership company that sells fun in the water, we sell boats, Yachts, Kayaks and also yacht WaterSport toys. We are looking to redesign our business cards in to something a little bit more sophisticated. in a way that we can make better use of our company colors. I'm attaching a zipped file containing the company 3 sets of company logo which one is an horizontal another one is a vertical and also a chromed 3d logo. Also is included two set of business cards that we use and also some designs that i think it's interesting. We use PMS 2026c Orange and PMS 7687C Blue. I would like to see at least two different options with the orange as accent and also using blue as an accent color. It's really important for the business cards to have a font option and size that is legible to most people. Our current website is wwww.coralpennant.com. Please visit if you want to have a better feeling of the Boat dealership
You can send Single sided or double side options. We are now using single sided but we may be open for a double side option if we really like the design.
Target Market(s)
Marine, boat sales, yacht sales, water toys sales/
Contact Information for Business Card
Name: Dale Whitcombe
Address: 212 North Fenwick Lane,
Port Merrin, ST 00123
Phone: 954-731-8842
Fax: 954:731-8843
Cell: 954-382-1490
Email: dw@coralpennant.com
Website: coralpennant.com
Requirements
Must have
- the current information of the business card provided.
logo
use the PMS Colors
Nice to have
- a touch of elegance and sophistication but simple
Should not have
- should not have any typography that is hard to read, the card should be simple but yet sophisticated.

```html
<!DOCTYPE html>
<html lang="en">
<head>
<meta charset="utf-8">
<title>Coral Pennant – Business Card</title>
<link rel="stylesheet" href="https://fonts.googleapis.com/css2?family=Poppins:wght@400;600;700&display=swap">
<style>
  :root {
    --backdrop: #1e1e1e;
    --brand-blue: #1f6fb5;
    --brand-orange: #ee8a24;
    --card-white: #ffffff;
    --text-grey: #4a4a4a;
    --rule-grey: #6d6d6d;
    --back-mark: #fcd940;
  }
  * { margin: 0; padding: 0; box-sizing: border-box; }
  html, body {
    width: 1125px; height: 1200px; overflow: hidden;
    background: var(--backdrop);
    font-family: "Poppins", sans-serif;
  }
  .card {
    position: absolute; left: 150px; width: 824px; height: 471px;
    overflow: hidden;
  }
  .card-front { top: 106px; background: var(--card-white); }
  .card-back { top: 638px; background: var(--brand-orange); }

  .swoosh { position: absolute; left: 0; top: 0; width: 824px; height: 471px; }

  .brand { position: absolute; display: flex; flex-direction: column; align-items: center; }
  .brand-front { left: 450px; top: 45px; width: 330px; }
  .brand-dot {
    width: 90px; height: 90px; border-radius: 50%;
    border: 9px solid var(--brand-blue);
  }
  .brand-name {
    margin-top: 22px; font-weight: 700; font-size: 28px; letter-spacing: 0.5px;
    color: var(--brand-blue); text-transform: uppercase; white-space: nowrap;
  }
  .brand-back { left: 0; top: 118px; width: 824px; }
  .brand-back .brand-dot { width: 122px; height: 122px; border-width: 10px; border-color: var(--back-mark); }
  .brand-back .brand-name { margin-top: 40px; font-size: 38px; color: var(--back-mark); }

  .person-name {
    position: absolute; left: 47px; top: 264px;
    font-weight: 600; font-size: 25px; color: var(--brand-blue); text-transform: uppercase;
  }
  .divider {
    position: absolute; left: 48px; top: 315px; width: 730px; height: 1px;
    background: var(--rule-grey);
  }
  .contact-list {
    position: absolute; left: 47px; top: 335px; list-style: none;
    font-size: 18px; line-height: 24px; color: var(--text-grey);
  }
  .contact-list li { display: flex; align-items: center; }
  .contact-list svg { width: 15px; height: 15px; margin-right: 12px; fill: var(--brand-blue); }
  .address {
    position: absolute; right: 46px; top: 359px; text-align: right;
    font-size: 18px; line-height: 24px; color: var(--text-grey); font-style: normal;
  }
</style>
</head>
<body>
  <section class="card card-front">
    <svg class="swoosh" viewBox="0 0 800 457" preserveAspectRatio="none" aria-hidden="true">
      <path d="M0,0 H620 C380,25 110,85 0,172 Z" fill="#1f6fb5"/>
      <path d="M0,228 C55,140 250,62 615,0 C300,50 75,125 0,192 Z" fill="#ee8a24"/>
    </svg>

    <div class="brand brand-front">
      <div class="brand-dot"></div>
      <div class="brand-name">Coral Pennant</div>
    </div>

    <h1 class="person-name">Dale Whitcombe</h1>
    <div class="divider"></div>

    <ul class="contact-list">
      <li><svg viewBox="0 0 16 16"><path d="M3.5 1l2.5 3-1.5 2c1 2 3 4 5 5l2-1.5 3 2.5-1.5 2.5C7 15 1 9 1 2.5z"/></svg>555-731-8842</li>
      <li><svg viewBox="0 0 16 16"><path d="M4 0h8a1 1 0 0 1 1 1v14a1 1 0 0 1-1 1H4a1 1 0 0 1-1-1V1a1 1 0 0 1 1-1zm1 2v10h6V2zm3 11a1 1 0 1 0 0 2 1 1 0 0 0 0-2z"/></svg>555-382-1490</li>
      <li><svg viewBox="0 0 16 16"><path d="M4 1h8v4H4zM1 6h14v7h-3v-3H4v3H1zm4 5h6v4H5z"/></svg>555-731-8843</li>
      <li><svg viewBox="0 0 16 16"><path d="M1 3h14v10H1zm1 1.2V5l6 4 6-4v-.8L8 8z"/></svg>dw@coralpennant.com</li>
    </ul>

    <address class="address">
      212 North Fenwick Lane<br>
      Port Merrin, ST 00123<br>
      www.coralpennant.com
    </address>
  </section>

  <section class="card card-back">
    <div class="brand brand-back">
      <div class="brand-dot"></div>
      <div class="brand-name">Coral Pennant</div>
    </div>
  </section>
</body>
</html>
```